Business Card for Fashion House

We need a business card design for our personalize fashion service for our customers. the business card should reflect reliability, luxury and creativity.
The brand Gravetto is extracted from "Graceful Velvetto"; Gravetto provides fashion designs sprinkled with luxury and style tailored for our elite clients character profile.
Gravetto is created for those who embody class and elegance with a passion for style.
Target Market(s)
Affluent Customers
Industry/Entity Type
Fashion
Contact Information for Business Card
Samira Haddadin
Fashion Designer
Telephone: +971 4 555 0192
Mobile +971 50 555 0147
Emal info@gravetto-example.com
Website www.gravetto-example.com
Social Media Youtube g+ Facebook Instagram Pin /gravetto
Font styles to use
Other font styles liked:
- Audrey provided
Look and feel
Each slider illustrates characteristics of the customer's brand and the style your logo design should communicate.

```html
<!DOCTYPE html>
<html lang="en">
<head>
<meta charset="utf-8">
<title>Gravetto — Business Card</title>
<link rel="stylesheet" href="https://fonts.googleapis.com/css2?family=Marcellus&family=Oswald:wght@300;500&family=Lato:wght@400&display=swap">
<style>
  :root {
    --backdrop: #e6e3e0;
    --card-dark: #2f2927;
    --card-light: #ffffff;
    --ink: #2b2624;
    --ink-soft: #4a4442;
    --paper-text: #f4f1ee;
    --shadow: rgba(0, 0, 0, 0.18);
  }
  * { box-sizing: border-box; margin: 0; padding: 0; }
  html, body {
    width: 1200px; height: 1000px; overflow: hidden;
    background: var(--backdrop);
  }
  .stage {
    position: relative; width: 1200px; height: 1000px;
  }
  .card {
    position: absolute; left: 250px; width: 700px; height: 400px;
    border-radius: 26px; box-shadow: 0 14px 30px var(--shadow);
    overflow: hidden;
  }
  .card--front { top: 60px; background: var(--card-dark); }
  .card--back  { top: 530px; background: var(--card-light); color: var(--ink); }

  /* brand lockup */
  .brand {
    position: absolute; display: flex; flex-direction: column; align-items: center;
    font-family: "Marcellus", serif; font-weight: 400;
  }
  .brand__mark {
    width: 44px; height: 44px; border: 3px solid currentColor; margin-bottom: 22px;
  }
  .brand__name { letter-spacing: 0.42em; text-transform: uppercase; }
  .card--front .brand { right: 70px; top: 130px; color: var(--paper-text); }
  .card--front .brand__name { font-size: 30px; }
  .card--back .brand { left: 70px; top: 60px; color: var(--ink); }
  .card--back .brand__name { font-size: 30px; }

  /* contacts */
  .contacts {
    position: absolute; left: 60px; bottom: 46px; list-style: none;
    font-family: "Lato", sans-serif; font-size: 17px; color: var(--ink);
  }
  .contacts li { display: flex; align-items: center; gap: 12px; margin-top: 6px; }
  .contacts svg { width: 16px; height: 16px; flex: none; }

  /* social */
  .social {
    position: absolute; right: 60px; top: 62px; display: flex; align-items: center; gap: 8px;
    font-family: "Lato", sans-serif; font-size: 17px; color: var(--ink);
  }
  .social__dot { width: 18px; height: 18px; border-radius: 50%; background: var(--ink); }
  .social__handle { margin-left: 4px; }

  .accent-block {
    position: absolute; right: 0; top: 140px; width: 46px; height: 46px; background: var(--ink);
  }

  .person {
    position: absolute; right: 70px; top: 150px; text-align: right;
    font-family: "Oswald", sans-serif; color: var(--ink);
  }
  .person__name { font-size: 30px; font-weight: 300; letter-spacing: 0.02em; text-transform: uppercase; }
  .person__name strong { font-weight: 500; }
  .person__role { font-family: "Marcellus", serif; font-size: 17px; color: var(--ink-soft); margin-top: 2px; }
</style>
</head>
<body>
<main class="stage">
  <section class="card card--front" aria-label="Card front">
    <div class="brand">
      <span class="brand__mark" aria-hidden="true"></span>
      <span class="brand__name">Gravetto</span>
    </div>
  </section>

  <section class="card card--back" aria-label="Card back">
    <div class="brand">
      <span class="brand__mark" aria-hidden="true"></span>
      <span class="brand__name">Gravetto</span>
    </div>

    <div class="social" aria-label="Social media">
      <span class="social__dot"></span>
      <span class="social__dot"></span>
      <span class="social__dot"></span>
      <span class="social__dot"></span>
      <span class="social__dot"></span>
      <span class="social__handle">/gravetto</span>
    </div>

    <span class="accent-block" aria-hidden="true"></span>

    <div class="person">
      <p class="person__name">Samira <strong>Haddadin</strong></p>
      <p class="person__role">Fashion Designer</p>
    </div>

    <ul class="contacts">
      <li>
        <svg viewBox="0 0 16 16" aria-hidden="true"><rect x="4" y="1" width="8" height="14" rx="1.5" fill="none" stroke="currentColor" stroke-width="1.5"/><circle cx="8" cy="12.5" r="0.9" fill="currentColor"/></svg>
        <span>+971 4 555 0192</span>
      </li>
      <li>
        <svg viewBox="0 0 16 16" aria-hidden="true"><path d="M3 2l3 0 1 3.5-2 1.3a8 8 0 0 0 4.2 4.2l1.3-2 3.5 1v3a1 1 0 0 1-1 1A12 12 0 0 1 2 3a1 1 0 0 1 1-1z" fill="currentColor"/></svg>
        <span>+971 50 555 0147</span>
      </li>
      <li>
        <svg viewBox="0 0 16 16" aria-hidden="true"><circle cx="8" cy="8" r="6.5" fill="none" stroke="currentColor" stroke-width="1.4"/><ellipse cx="8" cy="8" rx="2.8" ry="6.5" fill="none" stroke="currentColor" stroke-width="1.2"/><line x1="1.5" y1="8" x2="14.5" y2="8" stroke="currentColor" stroke-width="1.2"/></svg>
        <span>www.gravetto-example.com</span>
      </li>
      <li>
        <svg viewBox="0 0 16 16" aria-hidden="true"><rect x="1.5" y="3.5" width="13" height="9" fill="none" stroke="currentColor" stroke-width="1.4"/><path d="M1.5 3.5l6.5 5 6.5-5" fill="none" stroke="currentColor" stroke-width="1.4"/></svg>
        <span>info@gravetto-example.com</span>
      </li>
    </ul>
  </section>
</main>
</body>
</html>
```